Online interactive calendar for training organisation

We have a new website being made and need a design for an online calendar that is interactive and very simple and easy to use. On our main page this calendar will include all of our courses (approx 30 different ones with up to 8 different locations). On our sub pages which have course information, the calendar will only include details of that specific course. Details needed are: Course code, course name/title, date, duration (1/2 day - 5 days), location, price, discount price. Maybe also a key for available or limited spots left? We want a section at the top of the calendar to be able to filter by location or course, and maybe to filter by month also? I have included a spreadsheet with a sample of our courses with this information. Also a sample draft of the main page on our new webpage to show the colour green which is our company colour. Main notes - we want as simple, effective and easy to use as possible.
We will need to know what plug in we can use to get the design you have created.

Target Market(s)

Mining and construction - both companies and individuals

Number of Pages Required

1 page

Colors
cadf82

Requirements
Must have
• Be simple, easy to use, effective.

```html
<!DOCTYPE html>
<html lang="en">
<head>
<meta charset="utf-8">
<title>Course Calendar</title>
<link href="https://fonts.googleapis.com/css2?family=Montserrat:wght@400;600;700&display=swap" rel="stylesheet">
<style>
  :root {
    --brand: #cadf82;
    --ink: #222222;
    --muted: #555555;
    --line: #e6e6e6;
    --alert: #e0201b;
    --bg: #ffffff;
  }
  * { box-sizing: border-box; margin: 0; padding: 0; }
  html, body { width: 1200px; height: 837px; overflow: hidden; background: var(--bg); }
  body { font-family: "Montserrat", Arial, sans-serif; color: var(--ink); position: relative; }

  .calendar-title {
    position: absolute; top: 110px; left: 0; width: 1200px;
    text-align: center; font-size: 36px; font-weight: 700; letter-spacing: 1px;
  }

  .filter-bar {
    position: absolute; top: 184px; left: 90px; width: 1020px; height: 48px;
    border: 1px solid var(--line); display: flex;
  }
  .filter { flex: 1; padding: 5px 12px; position: relative; border-right: 1px solid var(--line); }
  .filter:last-child { border-right: none; }
  .filter-label { font-size: 13.5px; font-weight: 400; color: var(--muted); letter-spacing: .3px; }
  .filter-value { font-size: 15px; font-weight: 700; margin-top: 2px; letter-spacing: .3px; }
  .filter-caret { position: absolute; right: 12px; top: 30px; }

  .rule { position: absolute; top: 244px; left: 90px; width: 1020px; border-top: 1px solid var(--line); }

  .course-grid {
    position: absolute; top: 260px; left: 90px; width: 1020px;
    display: grid; grid-template-columns: repeat(3, 339px); column-gap: 2px; row-gap: 15px;
  }
  .course-card {
    height: 221px; border: 1px solid var(--line); border-left: 6px solid var(--brand);
    padding: 11px 0 0 16px; font-size: 15.5px;
  }
  .course-code, .course-name { font-weight: 700; font-size: 15px; letter-spacing: .3px; }
  .course-name { margin-top: 19px; }
  .limited { color: var(--alert); font-weight: 400; }
  .detail { display: flex; align-items: center; gap: 8px; margin-top: 17px; line-height: 19px; }
  .detail svg { flex: none; }
  .price { margin-top: 16px; display: flex; align-items: baseline; gap: 10px; padding-left: 2px; }
  .price-was { text-decoration: line-through; font-size: 15px; color: var(--ink); }
  .price-now { font-weight: 700; font-size: 19.5px; }
  .price-solo { padding-left: 6px; }

  .legend { position: absolute; top: 744px; left: 90px; font-size: 15.5px; letter-spacing: .3px; }
  .legend .limited { margin-right: 12px; }
</style>
</head>
<body>
  <h1 class="calendar-title">CALENDAR</h1>

  <div class="filter-bar">
    <div class="filter">
      <div class="filter-label">LOCATION</div>
      <div class="filter-value">YATALA</div>
      <svg class="filter-caret" width="11" height="7" viewBox="0 0 11 7"><path d="M0 0h11L5.5 7z" fill="var(--ink)"/></svg>
    </div>
    <div class="filter">
      <div class="filter-label">COURSE</div>
      <div class="filter-value">SELECT</div>
      <svg class="filter-caret" width="11" height="7" viewBox="0 0 11 7"><path d="M0 0h11L5.5 7z" fill="var(--ink)"/></svg>
    </div>
    <div class="filter">
      <div class="filter-label">MONTH</div>
      <div class="filter-value">SELECT</div>
      <svg class="filter-caret" width="11" height="7" viewBox="0 0 11 7"><path d="M0 0h11L5.5 7z" fill="var(--ink)"/></svg>
    </div>
  </div>
  <div class="rule"></div>

  <svg width="0" height="0" style="position:absolute">
    <defs>
      <symbol id="icon-date" viewBox="0 0 16 16"><rect x="1.5" y="2.5" width="13" height="12" fill="none" stroke="#cadf82" stroke-width="1.5"/><path d="M1.5 5.5h13M4.5 1v3M11.5 1v3" stroke="#cadf82" stroke-width="1.5"/><path d="M4 8h2v1.5H4zM7 8h2v1.5H7zM10 8h2v1.5h-2zM4 11h2v1.5H4zM7 11h2v1.5H7zM10 11h2v1.5h-2z" fill="#cadf82"/></symbol>
      <symbol id="icon-time" viewBox="0 0 16 16"><circle cx="8" cy="8" r="6.8" fill="none" stroke="#cadf82" stroke-width="1.6"/><path d="M8 4v4.3l2.8 1.8" fill="none" stroke="#cadf82" stroke-width="1.6"/></symbol>
      <symbol id="icon-duration" viewBox="0 0 16 16"><path d="M2.5 1h11v1.5h-1.2c0 3-2.2 4.3-3 5.5.8 1.2 3 2.5 3 5.5h1.2V15h-11v-1.5h1.2c0-3 2.2-4.3 3-5.5-.8-1.2-3-2.5-3-5.5H2.5z" fill="#cadf82"/></symbol>
    </defs>
  </svg>

  <div class="course-grid">
    <article class="course-card">
      <div class="course-code">RIIHAN304D <span class="limited">*</span></div>
      <div class="course-name">WORK SAFELY AT HEIGHTS</div>
      <div class="detail"><svg width="16" height="16"><use href="#icon-date"/></svg>Tuesday, October 29, 2019</div>
      <div class="detail"><svg width="16" height="16"><use href="#icon-time"/></svg>TIme: 8 am</div>
      <div class="detail"><svg width="16" height="16"><use href="#icon-duration"/></svg>Duration: 1 day</div>
      <div class="price"><span class="price-was">$500.00</span><span class="price-now">$120.00</span></div>
    </article>
    <article class="course-card">
      <div class="course-code">RIIHAN304D</div>
      <div class="course-name">WORK SAFELY AT HEIGHTS</div>
      <div class="detail"><svg width="16" height="16"><use href="#icon-date"/></svg>Tuesday, October 29, 2019</div>
      <div class="detail"><svg width="16" height="16"><use href="#icon-time"/></svg>TIme: 8 am</div>
      <div class="detail"><svg width="16" height="16"><use href="#icon-duration"/></svg>Duration: 1 day</div>
      <div class="price"><span class="price-was">$500.00</span><span class="price-now">$120.00</span></div>
    </article>
    <article class="course-card">
      <div class="course-code">HLTAID005</div>
      <div class="course-name">CONFINED SPACE - PRACTICAL ONLY</div>
      <div class="detail"><svg width="16" height="16"><use href="#icon-date"/></svg>Thursday, January 30, 2020</div>
      <div class="detail"><svg width="16" height="16"><use href="#icon-time"/></svg>TIme: 1 pm</div>
      <div class="detail"><svg width="16" height="16"><use href="#icon-duration"/></svg>Duration: 1/2 day</div>
      <div class="price price-solo"><span class="price-now">$80.00</span></div>
    </article>
    <article class="course-card">
      <div class="course-code">HLTAID001</div>
      <div class="course-name">FIRST AID - PRACTICAL ONLY</div>
      <div class="detail"><svg width="16" height="16"><use href="#icon-date"/></svg>Friday, November 15, 2019</div>
      <div class="detail"><svg width="16" height="16"><use href="#icon-time"/></svg>TIme: 1 pm</div>
      <div class="detail"><svg width="16" height="16"><use href="#icon-duration"/></svg>Duration: 1/2 day</div>
      <div class="price price-solo"><span class="price-now">$80.00</span></div>
    </article>
    <article class="course-card">
      <div class="course-code">CPCCCM208 <span class="limited">*</span></div>
      <div class="course-name">DOGGING</div>
      <div class="detail"><svg width="16" height="16"><use href="#icon-date"/></svg>Monday, October 28, 2019</div>
      <div class="detail"><svg width="16" height="16"><use href="#icon-time"/></svg>TIme: 8 am</div>
      <div class="detail"><svg width="16" height="16"><use href="#icon-duration"/></svg>Duration: 10 day</div>
      <div class="price"><span class="price-was">$2,300.00</span><span class="price-now">$1,200.00</span></div>
    </article>
    <article class="course-card">
      <div class="course-code">TLILIC0005 <span class="limited">*</span></div>
      <div class="course-name">FRONT END LOADER BUNDLE</div>
      <div class="detail"><svg width="16" height="16"><use href="#icon-date"/></svg>Monday, October 28, 2019</div>
      <div class="detail"><svg width="16" height="16"><use href="#icon-time"/></svg>TIme: 8 am</div>
      <div class="detail"><svg width="16" height="16"><use href="#icon-duration"/></svg>Duration: 10 day</div>
      <div class="price"><span class="price-was">$2,300.00</span><span class="price-now">$1,200.00</span></div>
    </article>
  </div>

  <p class="legend"><span class="limited">*</span><span style="margin-right:12px">-</span>LIMITED SPOTS LEFT</p>
</body>
</html>
```